BrightLedgerMoney(.com) needs website & logo design

We need our website mock-up made into a reality! We are wanting to launch a multifaceted website for all things financial - i.e. blogs, financial wellness information, and a network of redirect links.
We have an existing mock-up, which I will include, but are open to your creative approach!

Industry/Entity Type

Finance

Coding

Coded - Design and coding required

Number of Pages Required

1 page

Requirements
Must have
• Corresponding logo

```html
<!DOCTYPE html>
<html lang="en">
<head>
<meta charset="utf-8">
<title>Bright Ledger Money</title>
<link href="https://fonts.googleapis.com/css2?family=Oswald:wght@500;600&family=Roboto:wght@400;500;700&display=swap" rel="stylesheet">
<style>
:root{
  --teal:#72d9c0;
  --teal-dark:#5cc7ad;
  --purple:#a08bcb;
  --purple-soft:#d6cbea;
  --ink:#222226;
  --text:#4a4a4f;
  --muted:#8a8a90;
  --paper:#ffffff;
  --mist:#f3f3f4;
  --night:#1f1b20;
}
*{margin:0;padding:0;box-sizing:border-box}
html,body{width:1200px;height:4409px;overflow:hidden}
body{position:relative;background:var(--paper);font-family:"Roboto",Arial,sans-serif;color:var(--text)}
.abs{position:absolute}
.heading{font-family:"Oswald","Arial Narrow",sans-serif;font-weight:600;color:var(--ink);text-transform:uppercase;letter-spacing:.5px}
.btn{position:absolute;display:flex;align-items:center;justify-content:center;gap:10px;border-radius:24px;color:#fff;font-size:14px;font-weight:700;text-transform:uppercase;height:44px}
.btn .dot{width:13px;height:13px;border-radius:50%;background:#fff;position:relative}
.btn .dot::after{content:"";position:absolute;left:4px;top:3.5px;border-left:5px solid currentColor;border-top:3px solid transparent;border-bottom:3px solid transparent}
.btn-purple{background:var(--purple)}
.btn-purple .dot::after{border-left-color:var(--purple)}
.btn-teal{background:var(--teal)}
.btn-teal .dot::after{border-left-color:var(--teal)}
.photo{position:absolute}

/* header */
.brand{font-family:"Roboto",Arial,sans-serif;font-weight:700;font-size:29px;color:var(--ink);letter-spacing:.3px}
.nav{position:absolute;top:32px;left:485px;display:flex;gap:27px;font-size:14px;color:var(--ink)}
.nav .active{color:var(--teal-dark)}
.login{left:943px;top:20px;width:145px;border-radius:22px}

/* hero */
.hero-title{left:110px;top:275px;font-size:43px;line-height:48px;color:#fff;text-shadow:0 2px 6px rgba(0,0,0,.25)}

/* why choose us */
.section-title{width:1200px;text-align:center;font-size:36px}
.bubble{position:absolute;border-radius:50%;color:#fff;text-align:center;display:flex;flex-direction:column;align-items:center}
.bubble h3{font-size:19px;font-weight:700;margin-top:12px}
.bubble p{font-size:13px;line-height:20px;margin-top:12px;width:230px;opacity:.92}
.bubble .chev{margin-top:22px}
.arrow-side{position:absolute;top:1052px;width:16px;height:16px;border-left:3px solid var(--ink);border-bottom:3px solid var(--ink)}

/* trending */
.body-copy{font-size:14.5px;line-height:25.5px;color:var(--text);text-align:justify}

/* topics */
.topic{position:absolute;top:2060px;width:150px;text-align:center}
.topic .ring{width:130px;height:130px;margin:0 auto;border-radius:50%;display:flex;align-items:center;justify-content:center}
.topic .core{width:100px;height:100px;border-radius:50%;background:#fff;display:flex;align-items:center;justify-content:center}
.topic span{display:block;margin-top:26px;font-size:15px;font-weight:700;color:var(--ink)}

/* blog */
.card{position:absolute;top:3430px;width:309px;height:385px;background:#fff;border-radius:6px;box-shadow:0 4px 18px rgba(0,0,0,.09);text-align:center}
.card .img{margin:7px;height:203px;border-radius:3px}
.card .date{margin-top:20px;font-size:12.5px;color:var(--teal-dark)}
.card h4{margin-top:10px;font-size:16px;color:var(--ink)}
.card p{margin:10px auto 0;width:270px;font-size:13.5px;line-height:22px;color:var(--muted)}
.card .more{margin-top:14px;font-size:14px;font-weight:700;color:var(--purple);display:flex;justify-content:center;align-items:center;gap:8px}
.card .more i{width:13px;height:13px;border-radius:50%;background:var(--purple);position:relative}
.card .more i::after{content:"";position:absolute;left:4.5px;top:3.5px;border-left:5px solid #fff;border-top:3px solid transparent;border-bottom:3px solid transparent}

/* footer */
.footer-col h5{font-size:17px;font-weight:700;color:#fff;margin-bottom:18px}
.footer-col li{list-style:none;font-size:13.5px;color:#e6e6e6;margin-bottom:17px;padding-left:20px;position:relative}
.footer-col li::before{content:"»";position:absolute;left:0;color:#fff}
.contact-line{position:absolute;font-size:13px;line-height:22px;color:#e6e6e6;padding-left:32px}
.social{display:flex;gap:8px}
.social span{width:35px;height:35px;border-radius:50%;background:#fff}
</style>
</head>
<body>

<!-- hero photo -->
<div class="photo" role="img" aria-label="Young woman lying on grass smiling at a laptop" style="left:0;top:0;width:1200px;height:760px;background:linear-gradient(180deg,#eef0ee 0%,#d9ddd6 30%,#9fb27a 60%,#6f8f3e 100%)"></div>
<svg class="abs" style="left:0;top:660px" width="1200" height="110" viewBox="0 0 1200 110">
  <polygon points="0,60 690,20 1200,95 1200,110 0,110" fill="#fff"/>
  <polygon points="690,20 1200,70 1200,95" fill="var(--teal)"/>
</svg>

<!-- header -->
<div class="abs brand" style="left:110px;top:24px">BRIGHT LEDGER MONEY</div>
<nav class="nav">
  <span class="active">HOME</span><span>ABOUT US</span><span>SERVICES</span><span>BLOG</span><span>CONTACT US</span>
</nav>
<div class="btn btn-teal login">LOGIN
  <svg width="12" height="13" viewBox="0 0 12 13"><circle cx="6" cy="3.5" r="3.2" fill="#fff"/><path d="M0 13c0-4 2.5-6 6-6s6 2 6 6z" fill="#fff"/></svg>
</div>

<h1 class="abs heading hero-title">A clear path to<br>financial wellness</h1>
<div class="btn btn-purple" style="left:110px;top:408px;width:172px">GET STARTED <span class="dot"></span></div>

<!-- why choose us -->
<h2 class="abs heading section-title" style="top:796px">Why choose us</h2>
<svg class="abs" style="left:0;top:1040px" width="1200" height="200" viewBox="0 0 1200 200" aria-hidden="true">
  <path d="M0 60 C300 160 500 0 800 90 S1100 40 1200 100" fill="none" stroke="#e3e3e3" stroke-width="1"/>
  <path d="M0 80 C300 180 500 20 800 110 S1100 60 1200 120" fill="none" stroke="#ececec" stroke-width="1"/>
</svg>
<span class="arrow-side" style="left:52px;transform:rotate(45deg)"></span>
<span class="arrow-side" style="left:1134px;transform:rotate(-135deg)"></span>

<div class="bubble" style="left:112px;top:880px;width:348px;height:348px;background:var(--teal);padding-top:52px">
  <svg width="64" height="64" viewBox="0 0 64 64" fill="none" stroke="#fff" stroke-width="2.5"><rect x="14" y="6" width="36" height="52" rx="4"/><rect x="20" y="12" width="24" height="12"/><circle cx="24" cy="34" r="2"/><circle cx="32" cy="34" r="2"/><circle cx="40" cy="34" r="2"/><circle cx="24" cy="44" r="2"/><circle cx="32" cy="44" r="2"/><circle cx="40" cy="44" r="2"/></svg>
  <h3>Budget</h3>
  <p>Lorem ipsum dolor sit amet, consectetur adipiscing elit, sed do eiusmod tempor labore</p>
  <svg class="chev" width="42" height="42" viewBox="0 0 42 42" fill="none" stroke="#fff" stroke-width="2"><circle cx="21" cy="21" r="19"/><path d="M13 17l8 8 8-8"/></svg>
</div>
<div class="bubble" style="left:740px;top:880px;width:348px;height:348px;background:var(--teal);padding-top:52px">
  <svg width="64" height="64" viewBox="0 0 64 64" fill="none" stroke="#fff" stroke-width="2.5"><rect x="10" y="6" width="28" height="52" rx="4"/><line x1="10" y1="46" x2="38" y2="46"/><circle cx="46" cy="18" r="10"/><path d="M41 18l4 4 6-7"/></svg>
  <h3>Track</h3>
  <p>Lorem ipsum dolor sit amet, consectetur adipiscing elit, sed do eiusmod tempor labore</p>
  <svg class="chev" width="42" height="42" viewBox="0 0 42 42" fill="none" stroke="#fff" stroke-width="2"><circle cx="21" cy="21" r="19"/><path d="M13 17l8 8 8-8"/></svg>
</div>
<div class="bubble" style="left:424px;top:889px;width:352px;height:352px;background:var(--purple);border:6px solid #fff;box-shadow:0 6px 22px rgba(0,0,0,.18);padding-top:50px">
  <svg width="64" height="64" viewBox="0 0 64 64" fill="none" stroke="#fff" stroke-width="2.5"><rect x="8" y="6" width="30" height="44" rx="3"/><rect x="13" y="11" width="20" height="9"/><circle cx="36" cy="46" r="11"/><path d="M36 40v12M33 43h5a2 2 0 010 4h-4a2 2 0 000 4h5"/><line x1="44" y1="20" x2="56" y2="20"/><line x1="44" y1="28" x2="56" y2="28"/></svg>
  <h3>Calculate</h3>
  <p>Lorem ipsum dolor sit amet, consectetur adipiscing elit, sed do eiusmod tempor labore et dolore magna aliqua.</p>
  <svg class="chev" width="42" height="42" viewBox="0 0 42 42" fill="none" stroke="#fff" stroke-width="2"><circle cx="21" cy="21" r="19"/><path d="M13 17l8 8 8-8"/></svg>
</div>

<!-- trending -->
<div class="abs" style="left:0;top:1328px;width:1200px;height:640px;background:var(--mist)"></div>
<div class="photo" role="img" aria-label="Thoughtful man with glasses at a laptop beside the sea" style="left:0;top:1328px;width:600px;height:640px;background:linear-gradient(90deg,#3a4660 0%,#7d8fa8 45%,#c9d3de 75%,rgba(243,243,244,0) 100%)"></div>
<svg class="abs" style="left:0;top:1925px" width="1200" height="80" viewBox="0 0 1200 80">
  <polygon points="0,45 0,80 1200,80 1200,45 600,0" fill="#fff"/>
  <polygon points="0,45 600,0 0,75" fill="var(--teal)"/>
</svg>
<h2 class="abs heading" style="left:597px;top:1402px;font-size:36px;line-height:44px">Trending in 2021:<br>Financial literacy</h2>
<div class="abs" style="left:597px;top:1506px;width:491px">
  <p class="body-copy">Lorem ipsum dolor sit amet, consectetur adipiscing elit, sed do eiusmod tempor incididunt ut labore et dolore magna aliqua. Ut enim ad minim veniam, quis nostrud exercitation ullamco laboris nisi ut aliquip ex ea commodo consequat. Duis aute irure dolor in reprehenderit in voluptate velit esse cillum dolore eu fugiat nulla pariatur. Excepteur sint occaecat cupidatat non proident, sunt in culpa qui officia deserunt.</p>
  <p class="body-copy" style="margin-top:13px">Lorem ipsum dolor sit amet, consectetur adipiscing elit, sed do eiusmod tempor incididunt ut labore et dolore magna aliqua. Ut enim ad minim veniam, quis nostrud exercitation ullamco laboris nisi ut aliquip ex ea commodo consequat Duis aute irure dolor in reprehenderited.</p>
</div>
<div class="btn btn-purple" style="left:597px;top:1810px;width:163px">LEARN MORE <span class="dot"></span></div>

<!-- topics -->
<div class="topic" style="left:102px"><div class="ring" style="background:var(--purple-soft)"><div class="core" style="border:8px solid var(--purple)">
  <svg width="50" height="50" viewBox="0 0 50 50" fill="none" stroke="var(--purple)" stroke-width="2.5"><circle cx="24" cy="26" r="18"/><circle cx="24" cy="26" r="11"/><circle cx="24" cy="26" r="4"/><path d="M24 26L42 8"/></svg>
</div></div><span>Set Goals</span></div>
<div class="topic" style="left:271px"><div class="ring" style="background:#c9f0e6"><div class="core" style="border:8px solid var(--teal)">
  <svg width="50" height="50" viewBox="0 0 50 50" fill="none" stroke="var(--teal-dark)" stroke-width="2.5"><path d="M18 8h14l-4 8h-6z"/><path d="M20 16C8 24 8 44 25 44s17-20 5-28"/><path d="M25 23v16M21 27h6a2.5 2.5 0 010 5h-4a2.5 2.5 0 000 5h6"/></svg>
</div></div><span>Money 101</span></div>
<div class="topic" style="left:440px"><div class="ring" style="background:var(--purple-soft)"><div class="core" style="border:8px solid var(--purple)">
  <svg width="50" height="50" viewBox="0 0 50 50" fill="none" stroke="var(--purple)" stroke-width="2.5"><rect x="8" y="6" width="26" height="36" rx="2"/><line x1="13" y1="16" x2="28" y2="16"/><line x1="13" y1="23" x2="24" y2="23"/><circle cx="34" cy="36" r="9"/><path d="M34 31v10"/></svg>
</div></div><span>Budgeting</span></div>
<div class="topic" style="left:609px"><div class="ring" style="background:#c9f0e6"><div class="core" style="border:8px solid var(--teal)">
  <svg width="50" height="50" viewBox="0 0 50 50" fill="none" stroke="var(--teal-dark)" stroke-width="2.5"><rect x="6" y="16" width="38" height="24" rx="3"/><line x1="6" y1="23" x2="44" y2="23"/><line x1="11" y1="33" x2="22" y2="33"/></svg>
</div></div><span>Credit Mindfulness</span></div>
<div class="topic" style="left:778px"><div class="ring" style="background:var(--purple-soft)"><div class="core" style="border:8px solid var(--purple)">
  <svg width="50" height="50" viewBox="0 0 50 50" fill="none" stroke="var(--purple)" stroke-width="2.5"><rect x="8" y="8" width="22" height="34" rx="2"/><rect x="12" y="12" width="14" height="7"/><rect x="30" y="22" width="14" height="20" rx="2"/><line x1="33" y1="28" x2="41" y2="28"/><line x1="33" y1="34" x2="41" y2="34"/></svg>
</div></div><span>Debt Management</span></div>
<div class="topic" style="left:946px"><div class="ring" style="background:#c9f0e6"><div class="core" style="border:8px solid var(--teal)">
  <svg width="50" height="50" viewBox="0 0 50 50" fill="none" stroke="var(--teal-dark)" stroke-width="2.5"><rect x="10" y="8" width="30" height="36" rx="3"/><rect x="18" y="5" width="14" height="6" rx="2"/><path d="M16 34l6-8 5 5 7-10"/></svg>
</div></div><span>Retirement Planning</span></div>

<!-- wellness 101 -->
<h2 class="abs heading" style="left:110px;top:2326px;font-size:37px">Financial wellness 101</h2>
<p class="abs body-copy" style="left:112px;top:2388px;width:468px">Lorem ipsum dolor sit amet, consectetur adipiscing elit, sed do eiusmod tempor incididunt ut labore et dolore magna aliqua. Ut enim ad minim veniam, quis nostrud exercitation ullamco laboris nisi ut aliquip ex ea commodo consequat. Duis aute irure dolor in reprehenderit in voluptate velit esse cillum dolore eu fugiat nulla pariatur. Excepteur sint occaecat cupidatat proident Lorem ipsum dolor sit amet, consectetur adipiscing elit, sed do eiusmod tempor incididunt ut labore et dolore magna aliqua. Ut enim ad minim veniam, quis nostrud exercitation ullamco laboris nisi ut aliquip ex ea commodo consequat Duis aute irure dolor in reprehenderited.</p>
<div class="btn btn-purple" style="left:112px;top:2665px;width:163px">LEARN MORE <span class="dot"></span></div>
<div class="abs" style="left:786px;top:2305px;width:414px;height:438px;background:var(--teal)"></div>
<div class="photo" role="img" aria-label="Woman in a sun hat sitting on a beach with a laptop under palm trees" style="left:673px;top:2331px;width:415px;height:385px;background:linear-gradient(180deg,#8fa0a8 0%,#b7b8a8 40%,#d8c6a6 70%,#cdb894 100%)"></div>

<!-- questions -->
<div class="photo" role="img" aria-label="Person working at a laptop on a seaside terrace, tinted purple" style="left:0;top:2828px;width:1200px;height:440px;background:linear-gradient(180deg,#a38fcd 0%,#9c88c8 60%,#8f7cbd 100%)"></div>
<svg class="abs" style="left:0;top:3215px" width="1200" height="90" viewBox="0 0 1200 90">
  <polygon points="0,55 600,8 1200,75 1200,90 0,90" fill="#fff"/>
  <polygon points="600,8 1200,50 1200,90" fill="var(--teal)"/>
</svg>
<h2 class="abs heading section-title" style="top:2895px;color:#fff;font-size:36px">Have any questions</h2>
<p class="abs" style="left:168px;top:2964px;width:864px;text-align:center;color:#fff;font-size:14.5px;line-height:26px">Lorem ipsum dolor sit amet, consectetur adipiscing elit, sed do eiusmod tempor incididunt ut labore et dolore magna aliqua. Ut enim ad minim veniam, quis nostrud exercitation ullamco laboris nisi ut aliquip ex ea commodo consequat. Duis aute irure dolor in reprehenderit in voluptate velit esse cillum dolore eu fugiat nulla pariatur. Excepteur sint occaecat cupidatat non proident, sunt in culpa qui officia deserunt mollit anim id est laborum.</p>
<div class="btn btn-teal" style="left:518px;top:3102px;width:163px">LEARN MORE <span class="dot"></span></div>

<!-- blog -->
<h2 class="abs section-title" style="top:3350px;font-family:'Oswald','Arial Narrow',sans-serif;font-weight:500;font-size:36px;color:var(--ink)">Our Blog</h2>
<div class="card" style="left:108px">
  <div class="img" role="img" aria-label="Calculator and small model house on a desk" style="background:linear-gradient(135deg,#3b3a38,#a68a62 60%,#e4ddd2)"></div>
  <div class="date">&#9638; March 23, 2023</div><h4>Lorem ipsum dolor sit amet</h4>
  <p>Lorem ipsum dolor sit amet, consectetur adipiscing elit, sed eiusmod</p><div class="more">READ MORE <i></i></div>
</div>
<div class="card" style="left:446px">
  <div class="img" role="img" aria-label="Hand dropping a coin into a piggy bank beside coin stacks" style="background:linear-gradient(135deg,#8a7a60,#d9c9a8 55%,#f2ece1)"></div>
  <div class="date">&#9638; March 23, 2023</div><h4>Lorem ipsum dolor sit amet</h4>
  <p>Lorem ipsum dolor sit amet, consectetur adipiscing elit, sed eiusmod</p><div class="more">READ MORE <i></i></div>
</div>
<div class="card" style="left:783px">
  <div class="img" role="img" aria-label="Colleagues reviewing financial charts with a tablet" style="background:linear-gradient(135deg,#2f3440,#7f8aa0 55%,#d8dde6)"></div>
  <div class="date">&#9638; March 23, 2023</div><h4>Lorem ipsum dolor sit amet</h4>
  <p>Lorem ipsum dolor sit amet, consectetur adipiscing elit, sed eiusmod</p><div class="more">READ MORE <i></i></div>
</div>

<!-- footer -->
<svg class="abs" style="left:0;top:3900px" width="1200" height="80" viewBox="0 0 1200 80">
  <polygon points="0,22 600,75 0,45" fill="var(--teal)"/>
  <polygon points="0,45 600,75 1200,20 1200,80 0,80" fill="var(--night)"/>
</svg>
<div class="abs" style="left:0;top:3979px;width:1200px;height:430px;background:var(--night)"></div>
<div class="abs brand" style="left:108px;top:4082px;font-size:25px;color:#fff">BRIGHT LEDGER MONEY</div>
<div class="abs social" style="left:135px;top:4150px"><span></span><span></span><span></span><span></span><span></span></div>

<div class="abs footer-col" style="left:470px;top:4090px"><h5>Quick Links</h5><ul><li>Home</li><li>About Us</li><li>Services</li><li>Blog</li><li>Contact Us</li></ul></div>
<div class="abs footer-col" style="left:686px;top:4090px"><h5>Important</h5><ul><li>Terms of Use</li><li>Site Map</li><li>Privacy Policy</li><li>Disclaimer</li></ul></div>
<div class="abs footer-col" style="left:882px;top:4090px"><h5>Contact us</h5></div>
<div class="contact-line" style="left:882px;top:4132px;width:220px">1/155 Lorem ipsum dolor sit amet, consectetur elit,
  <svg class="abs" style="left:5px;top:4px" width="12" height="15" viewBox="0 0 12 15"><path d="M6 0a6 6 0 00-6 6c0 4 6 9 6 9s6-5 6-9a6 6 0 00-6-6z" fill="#fff"/><circle cx="6" cy="6" r="2" fill="var(--night)"/></svg></div>
<div class="contact-line" style="left:882px;top:4190px">+ (123) 456- 7890
  <svg class="abs" style="left:5px;top:3px" width="10" height="16" viewBox="0 0 10 16"><rect x="1" y="1" width="8" height="14" rx="1.5" fill="none" stroke="#fff" stroke-width="1.5"/><circle cx="5" cy="12" r="1" fill="#fff"/></svg></div>
<div class="contact-line" style="left:882px;top:4258px">first.last@brightledgermoney.com
  <svg class="abs" style="left:4px;top:6px" width="14" height="10" viewBox="0 0 14 10" fill="none" stroke="#fff" stroke-width="1.4"><rect x=".7" y=".7" width="12.6" height="8.6"/><path d="M.7 .7L7 5.5l6.3-4.8"/></svg></div>

<div class="abs" style="left:110px;top:4345px;width:978px;height:1px;background:#4a454c"></div>
<div class="abs" style="left:0;top:4365px;width:1200px;text-align:center;font-size:12.5px;color:#e6e6e6">© 2023 Bright Ledger Money. | All Rights Reserved |</div>
<svg class="abs" style="left:1121px;top:4283px" width="38" height="38" viewBox="0 0 38 38"><circle cx="19" cy="19" r="19" fill="var(--purple)"/><path d="M11 13h16v9H17l-4 3v-3h-2z" fill="#fff"/></svg>

</body>
</html>
```